Business Report Cover

We need a revamped quarterly report cover to send to our clients. We asset manage commercial and residential properties throughout the the United States. We use a .pdf version of a cover that we've used for years but would like a fresh updated look for 2018. The cover should include our company logo (KOV Enterprises) and a photo of the property as well as the Quarter/Year of the report.

```html
<!DOCTYPE html>
<html lang="en">
<head>
<meta charset="utf-8">
<title>Quarterly Operating Report – 1st Quarter 2018</title>
<link href="https://fonts.googleapis.com/css2?family=Mada:wght@400;500;700&display=swap" rel="stylesheet">
<style>
  :root {
    --backdrop: #e9e4dc;
    --paper: #ffffff;
    --brand-green: #3a8c5f;
    --brand-green-soft: rgba(58, 140, 95, 0.88);
    --brand-green-veil: rgba(58, 140, 95, 0.55);
    --ink: #111111;
    --on-green: #ffffff;
  }
  * { margin: 0; padding: 0; box-sizing: border-box; }
  html, body {
    width: 1200px;
    height: 1200px;
    overflow: hidden;
    background: var(--backdrop);
    font-family: "Mada", sans-serif;
  }
  .report-cover {
    position: absolute;
    left: 204px;
    top: 40px;
    width: 792px;
    height: 1120px;
    background: var(--paper);
    box-shadow: 0 2px 8px rgba(0, 0, 0, 0.18);
    overflow: hidden;
  }
  .report-title {
    position: absolute;
    right: 64px;
    top: 122px;
    text-align: right;
    color: var(--ink);
    font-weight: 500;
    font-size: 31px;
    line-height: 40px;
    letter-spacing: -0.5px;
    text-transform: uppercase;
  }
  .property-photo {
    position: absolute;
    left: 0;
    top: 281px;
    width: 792px;
    height: 463px;
    background: linear-gradient(180deg, #d9dadf 0%, #b9bcc3 30%, #55604f 55%, #6e3a2e 72%, #4a4a4c 86%, #3b3436 100%);
  }
  .accent-block-top {
    position: absolute;
    left: 476px;
    top: 233px;
    width: 316px;
    height: 95px;
    background: var(--brand-green-soft);
  }
  .accent-veil {
    position: absolute;
    left: 0;
    top: 680px;
    width: 316px;
    height: 64px;
    background: var(--brand-green-veil);
  }
  .year-panel {
    position: absolute;
    left: 0;
    top: 744px;
    width: 316px;
    height: 376px;
    background: var(--brand-green);
    color: var(--on-green);
  }
  .report-year {
    position: absolute;
    left: 0;
    width: 316px;
    top: 36px;
    text-align: center;
    font-size: 96px;
    font-weight: 500;
    line-height: 1;
    letter-spacing: -2px;
  }
  .property-address {
    position: absolute;
    left: 69px;
    top: 272px;
    font-style: normal;
    font-size: 18px;
    line-height: 25px;
    font-weight: 400;
  }
  .company-mark {
    position: absolute;
    right: 60px;
    top: 1040px;
    display: flex;
    align-items: center;
    gap: 8px;
    color: var(--ink);
    font-size: 26px;
    font-weight: 700;
    letter-spacing: 0.5px;
  }
  .company-mark .mark-dot {
    width: 12px;
    height: 12px;
    border-radius: 50%;
    background: var(--brand-green);
  }
</style>
</head>
<body>
  <main class="report-cover">
    <h1 class="report-title">Quarterly Operating Report<br>1st Quarter</h1>

    <div class="property-photo" role="img" aria-label="Photo of the property: a convenience store and fuel station canopy under a cloudy sky"></div>
    <div class="accent-block-top"></div>
    <div class="accent-veil"></div>

    <section class="year-panel">
      <div class="report-year">2018</div>
      <address class="property-address">
        Riverton Corner Market<br>
        4120 NE Cedar Park Dr.<br>
        Riverton, WA 98600
      </address>
    </section>

    <div class="company-mark">
      <span class="mark-dot"></span>
      <span class="mark-name">KOV Enterprises</span>
    </div>
  </main>
</body>
</html>
```